Stationery Design Project for Nimbora, Chicago

Nimbora, a street parking application which helps car drivers find a street parking spot by offering an ideal path along which to look for parking. This path is calculated by our algorithm based on data (e.g. historical data, baseball games schedule, etc.). Along this path the driver will find a spot and will also save 70% of the search time. Customer we target is reg. between 21 and 45 yo.

We envision something young, fresh, bright and original. Slightly abstract maybe. It should represent the idea and elements of finding street parking in the city, e.g. car(s), parking spot, people, city, etc. (just ideas!).

Logo is attached.

Requirement:
- Business Cards (2 Sided Full Color CMYK)
- Letterhead (1 Sided Full Color CMYK)
- Envelope (1 Sided Full Color CMYK)
- Sticker (1 Sided Full Color CMYK), round with a 2inch diameter.

Reason: We're starting to get more and more designs and need more time to look into all of them. Very exciting!! Thanks to everybody!

Hi all, we're in the process of selecting our favs. Though choices!!! Really good submissions. Will keep you posted and sorry for the delay.

Target Market(s)

Car drivers and owners between 21 and 45

Industry/Entity Type

Parking

Requirements
Must have
• Sticker should be round and include company URL nimbora.com and the new logo which we will attach soon.
Should not have
• Should not be too serious or boring.

```html
<!DOCTYPE html>
<html lang="en">
<head>
<meta charset="utf-8">
<title>Nimbora Business Card</title>
<link rel="stylesheet" href="https://fonts.googleapis.com/css2?family=Open+Sans:wght@400;600;700&display=swap">
<style>
  :root {
    --page-bg: #e4e5e7;
    --card-bg: #ffffff;
    --ink: #1c1c1c;
    --ink-soft: #2b2b2b;
    --brand-blue: #1766b5;
    --brand-blue-deep: #1f3f9c;
    --arc-dark: #1a1a1a;
    --photo-light: #c9cbcd;
    --photo-mid: #8e9297;
    --photo-dark: #5d6166;
  }
  * { margin: 0; padding: 0; box-sizing: border-box; }
  html, body { width: 954px; height: 1200px; overflow: hidden; }
  body {
    background: var(--page-bg);
    font-family: "Open Sans", Arial, sans-serif;
    color: var(--ink);
    position: relative;
  }
  .card {
    position: absolute;
    left: 71px;
    width: 798px;
    height: 457px;
    background: var(--card-bg);
    border-radius: 26px;
    overflow: hidden;
    box-shadow: 0 6px 14px rgba(0,0,0,0.25);
  }
  .card--front { top: 99px; }
  .card--back { top: 650px; }
  .swoosh { position: absolute; inset: 0; width: 798px; height: 457px; }
  .brand-mark {
    position: absolute;
    border-radius: 50%;
    background: radial-gradient(circle at 40% 35%, var(--brand-blue) 0%, var(--brand-blue-deep) 100%);
  }
  .brand-name {
    position: absolute;
    font-weight: 600;
    color: var(--ink-soft);
    line-height: 1;
    letter-spacing: 1px;
  }
  .card--front .brand-mark { left: 55px; top: 58px; width: 154px; height: 154px; }
  .card--front .brand-name { left: 236px; top: 90px; font-size: 84px; }
  .holder {
    position: absolute;
    left: 0; right: 0;
    top: 260px;
    padding-left: 56px;
    text-align: center;
    font-size: 24px;
    font-weight: 700;
  }
  .contact {
    position: absolute;
    left: 0; right: 0;
    top: 364px;
    padding-left: 56px;
    text-align: center;
    font-size: 19px;
    line-height: 28px;
  }
  .contact b { font-weight: 700; }
  .contact .sep { margin: 0 6px; }
  .street-photo {
    position: absolute;
    left: 52px; top: 80px;
    width: 475px; height: 297px;
    background: linear-gradient(160deg, var(--photo-light) 0%, var(--photo-mid) 50%, var(--photo-dark) 100%);
    -webkit-mask-image: radial-gradient(ellipse 62% 62% at 50% 50%, #000 60%, transparent 100%);
    mask-image: radial-gradient(ellipse 62% 62% at 50% 50%, #000 60%, transparent 100%);
  }
  .card--back .brand-mark { left: 577px; top: 222px; width: 100px; height: 100px; }
  .card--back .brand-name { left: 500px; top: 334px; font-size: 62px; }
</style>
</head>
<body>
  <section class="card card--front">
    <svg class="swoosh" viewBox="0 0 798 457" aria-hidden="true">
      <defs>
        <linearGradient id="bandFront" x1="0" y1="0" x2="1" y2="0">
          <stop offset="0" stop-color="#2a3f9a"/>
          <stop offset="1" stop-color="#1766b5"/>
        </linearGradient>
      </defs>
      <path d="M600 0 Q790 40 798 250 L798 0 Z" fill="url(#bandFront)"/>
      <path d="M585 0 Q775 45 795 255" fill="none" stroke="var(--arc-dark)" stroke-width="9"/>
      <path d="M568 0 Q760 50 790 258" fill="none" stroke="#8a8a8a" stroke-width="2"/>
    </svg>
    <div class="brand-mark" aria-hidden="true"></div>
    <div class="brand-name">Nimbora</div>
    <p class="holder">Your Name - Designation</p>
    <p class="contact">
      <b>t</b> : 123-456-7890 <span class="sep">|</span> <b>m</b> : 123-456-7890<br>
      <b>e</b> : name@website.com <span class="sep">|</span> <b>w</b> : www.website.com
    </p>
  </section>

  <section class="card card--back">
    <svg class="swoosh" viewBox="0 0 798 457" aria-hidden="true">
      <defs>
        <linearGradient id="bandBack" x1="0" y1="0" x2="1" y2="0">
          <stop offset="0" stop-color="#2a3f9a"/>
          <stop offset="1" stop-color="#1766b5"/>
        </linearGradient>
      </defs>
      <path d="M600 0 Q790 40 798 250 L798 0 Z" fill="url(#bandBack)"/>
      <path d="M585 0 Q775 45 795 255" fill="none" stroke="var(--arc-dark)" stroke-width="9"/>
      <path d="M568 0 Q760 50 790 258" fill="none" stroke="#8a8a8a" stroke-width="2"/>
    </svg>
    <div class="street-photo" role="img" aria-label="Photo of cars parked in bays along a city street"></div>
    <div class="brand-mark" aria-hidden="true"></div>
    <div class="brand-name">Nimbora</div>
  </section>
</body>
</html>
```